Business Card Re-Design/Update

We'd like to update out business cards. I've included our current "Style guide" which has the colour scheme of the organisation in it. I've also included the branding files with logos etc in them.

I've also included a copy of one of our existing cards so that you can see how ugly/dated they look. I'd like a fresh modern corporate look.

Target Market(s)

These are for our clients, potential clients, industry contacts - like all business cards

Contact Information for Business Card

Name
Position
Company Address - Level 1, 47 Fernby Street, Carlow Qld 4072
Direct Phone
mobile
Email
Website -www.korvalit.com.au
Logo

Colors

Designer to choose colors to be used in the design.

Requirements
Must have
• Main Logo
• Cards will need to be editable to be able to personalize them for each new employee.
Nice to have
• The MapOut, ShipWell, KeepSteady would be okay to have if they can be sensibly and professionally added to the look without detracting from the main imagery.
• Maybe they could go on the back of the card? will leave this to your creative discretion as to whether/where they fit.
Should not have
• Should not have decorative or script fonts

```html
<!DOCTYPE html>
<html lang="en">
<head>
<meta charset="utf-8">
<title>korvalIT business card</title>
<link rel="stylesheet" href="https://fonts.googleapis.com/css2?family=Arimo:wght@400;700&display=swap">
<style>
  :root {
    --page: #e9e9e9;
    --red: #c8161d;
    --red-deep: #a40d12;
    --red-bright: #d41a21;
    --ink: #1e1e1e;
    --grey: #555555;
    --white: #ffffff;
    --pink: #f3c4c6;
  }
  * { margin: 0; padding: 0; box-sizing: border-box; }
  html, body { width: 1200px; height: 960px; overflow: hidden; }
  body {
    background: var(--page);
    font-family: "Arimo", Arial, sans-serif;
    position: relative;
  }
  .card {
    position: absolute;
    width: 600px;
    height: 342px;
    box-shadow: 0 3px 6px rgba(0,0,0,0.25);
    overflow: hidden;
  }
  .card-front { left: 315px; top: 113px; background: var(--white); }
  .card-back {
    left: 311px; top: 472px;
    background: linear-gradient(180deg, var(--red-bright) 0%, var(--red-deep) 100%);
  }
  .front-pattern {
    position: absolute; inset: 0;
    background:
      radial-gradient(ellipse 60% 70% at 40% 20%, rgba(235,120,125,0.45), rgba(255,255,255,0) 70%),
      radial-gradient(ellipse 45% 40% at 92% 8%, rgba(230,110,115,0.45), rgba(255,255,255,0) 70%),
      linear-gradient(160deg, #fbe3e4 0%, #fdf2f2 50%, #f7f7f7 100%);
  }
  .brand {
    position: absolute;
    display: flex; align-items: center; gap: 10px;
    font-weight: 700; letter-spacing: -0.5px;
  }
  .brand-mark { display: block; background: currentColor; }
  .front-brand { left: 42px; top: 226px; color: var(--red); font-size: 32px; }
  .front-brand .brand-mark { width: 34px; height: 34px; }
  .contact { position: absolute; left: 328px; top: 52px; color: var(--grey); font-size: 14px; }
  .name { color: var(--red); font-size: 20px; font-weight: 700; letter-spacing: 0.3px; }
  .role { color: var(--ink); font-size: 15px; margin-top: 2px; }
  .address { margin-top: 28px; line-height: 18px; }
  .lines { list-style: none; margin-top: 12px; font-size: 13.5px; line-height: 19.2px; }
  .lines b { color: var(--red); }
  .rule { position: absolute; left: 107px; top: 275px; width: 454px; height: 2px; background: var(--red); }
  .web { position: absolute; left: 332px; top: 287px; font-size: 14px; color: var(--grey); letter-spacing: 0.4px; }
  .back-brand { left: 100px; top: 140px; color: var(--white); font-size: 50px; gap: 16px; }
  .back-brand .brand-mark { width: 60px; height: 60px; }
  .services { position: absolute; left: 52px; top: 276px; display: flex; gap: 30px; list-style: none; }
  .service { display: flex; align-items: center; gap: 7px; color: var(--white); font-size: 25px; font-weight: 700; }
  .service::before { content: ""; width: 22px; height: 22px; background: var(--white); }
</style>
</head>
<body>
  <section class="card card-front">
    <div class="front-pattern" role="img" aria-label="Soft red diamond and dot pattern background"></div>
    <div class="brand front-brand"><span class="brand-mark"></span>korvalIT</div>
    <div class="contact">
      <p class="name">MAREN TALBOT</p>
      <p class="role">Business Development Manager</p>
      <p class="address">Level 1, 47 Fernby Street<br>Carlow Qld 4072</p>
      <ul class="lines">
        <li><b>P:</b> +61 (0)7 3418 6020</li>
        <li><b>P:</b> +61 (0)7 3418 6027</li>
        <li><b>C:</b> +61 (0)412 557 394</li>
        <li><b>F:</b> +61 (0)7 3418 6099</li>
        <li><b>E:</b> mtalbot@korvalit.com.au</li>
      </ul>
    </div>
    <div class="rule"></div>
    <p class="web">WWW.KORVALIT.COM.AU</p>
  </section>

  <section class="card card-back">
    <div class="brand back-brand"><span class="brand-mark"></span>korvalIT</div>
    <ul class="services">
      <li class="service">MapOut</li>
      <li class="service">ShipWell</li>
      <li class="service">KeepSteady</li>
    </ul>
  </section>
</body>
</html>
```